Revise our price listr for 2023

Please see attached price list with new prices to revise.
Please include new logo
Please add the text: Please note that prices are subject to change without prior notice.
Please remove prices from equipment with operator
Please add Under Commercial stone:
Fill Dirt $16.
Please add under Decorative Stone:
3/4" Barn Red Stone $127.
3/4" Yellow Ocean Gravel $140.
3/4" Delaware River Gravel $110.
1" Nutmeg Pebble $97.
Price list sending via email and customer in our lobby
Landscape and construction supply

```html
<!DOCTYPE html>
<html lang="en">
<head>
<meta charset="utf-8">
<title>Ridgeway Supply – 2023 Material Price List</title>
<link rel="stylesheet" href="https://fonts.googleapis.com/css2?family=Rubik:wght@500;700;800&family=Poppins:wght@400;500;600&family=Oswald:wght@500&display=swap">
<style>
  :root{
    --maroon:#6b1d21;
    --green:#1e8c3a;
    --yellow:#f6d70c;
    --ink:#333333;
    --leader:#8a8a8a;
    --page:#f1f1f1;
    --white:#ffffff;
  }
  *{box-sizing:border-box;margin:0;padding:0}
  html,body{width:720px;height:1200px;overflow:hidden;background:var(--page)}
  body{position:relative;font-family:"Poppins",sans-serif;color:var(--ink)}

  .flyer{position:absolute;left:0;top:345px;width:720px;height:510px;background:var(--white);overflow:hidden;box-shadow:0 6px 18px rgba(0,0,0,.18)}
  .band{position:absolute;left:0;top:0;width:720px;height:171px;background:var(--maroon)}
  .shapes{position:absolute;left:0;top:0;width:720px;height:510px}

  .brand{position:absolute;left:0;top:18px;width:720px;display:flex;justify-content:center;align-items:center;gap:6px}
  .brand-dot{width:14px;height:14px;border-radius:50%;background:var(--green)}
  .brand-name{font-family:"Rubik",sans-serif;font-weight:700;font-size:19px;color:var(--maroon);letter-spacing:.5px}

  .headline{position:absolute;left:0;top:70px;width:720px;text-align:center;font-family:"Rubik",sans-serif;font-weight:800;font-size:34px;line-height:40px;color:var(--white);letter-spacing:-.3px}
  .headline .year{color:var(--yellow)}

  .pill{position:absolute;height:16px;border-radius:8px;background:var(--maroon);color:var(--white);font-family:"Rubik",sans-serif;font-weight:500;font-size:11px;line-height:16px;text-align:center}
  .pill.tall{height:28px;font-size:10.5px;line-height:12px;padding-top:2px}

  .list{position:absolute}
  .row{height:10.25px;display:flex;align-items:flex-end;font-size:6.5px;line-height:8px;white-space:nowrap}
  .row .label{flex:none}
  .row .leader{flex:1;border-bottom:1px dotted var(--leader);margin:0 10px 1.5px 3px}
  .price{flex:none;width:23px;height:8px;background:var(--green);color:var(--white);font-family:"Oswald",sans-serif;font-weight:500;font-size:6px;line-height:8px;text-align:center}
  .price sup{font-size:3.5px;vertical-align:2px}
  .price.wide{width:50px;font-size:5.5px}
  .price.quote{width:46px;font-size:5.5px}
  .row.strong .label{font-weight:600;color:#222}
  .row.small{height:7px;font-size:5px;line-height:6px;align-items:flex-start}

  .group{position:absolute;border:1px solid var(--maroon);border-radius:6px}
  .group-title{position:absolute;left:50%;top:-5px;transform:translateX(-50%);background:var(--white);padding:0 4px;font-size:6px;line-height:8px;font-weight:600;color:var(--maroon);white-space:nowrap}
  .group .list{left:4px;right:4px}

  .ticks{position:absolute;left:0;right:0;display:flex;justify-content:center;gap:6px;font-size:5.8px;line-height:8px;white-space:nowrap}
  .tick{flex:none;display:flex;align-items:center;gap:2.5px;white-space:nowrap}
  .tick svg{flex:none;width:5.5px;height:5.5px}

  .swatch{position:absolute;width:61px;height:61px;border-radius:50%;border:2.5px solid var(--maroon)}
  .swatch.stone{background:radial-gradient(circle at 40% 40%,#e6e4dc,#9d9a90)}
  .swatch.soil{background:radial-gradient(circle at 50% 50%,#4a2c22,#1d1210)}
  .swatch.sand{background:radial-gradient(circle at 45% 45%,#e2c79a,#c6a16a)}

  .notice{position:absolute;left:260px;top:451px;width:205px;height:22px;border-radius:5px;background:var(--green);color:var(--white);font-size:6.6px;line-height:8.5px;text-align:center;padding-top:2.5px}

  .note-green{position:absolute;left:505px;font-size:6px;line-height:8px;color:var(--green)}

  .tip{position:absolute;left:501px;top:430px;width:192px;height:43px;border-radius:7px;background:var(--maroon)}
  .tip-icon{position:absolute;left:6px;top:7px;width:30px;height:30px;border-radius:50%;background:linear-gradient(135deg,#f0f0f0,#c9c9c9)}
  .tip-title{position:absolute;left:54px;top:4px;font-family:"Rubik",sans-serif;font-weight:700;font-size:11.5px;line-height:14px;color:var(--yellow)}
  .tip-body{position:absolute;left:54px;top:19px;width:134px;font-size:4.5px;line-height:5.6px;color:var(--white)}

  .site{position:absolute;left:248px;top:486px;width:252px;text-align:center;font-family:"Poppins",sans-serif;font-weight:600;font-size:10px;line-height:14px;letter-spacing:2.6px;color:var(--white)}
</style>
</head>
<body>
<main class="flyer">
  <div class="band"></div>
  <svg class="shapes" viewBox="0 0 720 510" aria-hidden="true">
    <path fill="#ffffff" d="M176 0 H514 C498 0 492 16 484 36 C476 58 470 66 454 66 H236 C220 66 214 58 206 36 C198 16 192 0 176 0 Z"/>
    <rect x="22" y="115" width="210" height="420" rx="14" fill="#ffffff"/>
    <rect x="255" y="115" width="210" height="420" rx="14" fill="#ffffff"/>
    <rect x="495" y="115" width="209" height="420" rx="14" fill="#ffffff"/>
    <path fill="#1e8c3a" d="M246 510 C262 510 266 482 284 482 H464 C482 482 486 510 502 510 Z"/>
  </svg>

  <header class="brand">
    <span class="brand-dot"></span>
    <span class="brand-name">RIDGEWAY SUPPLY</span>
  </header>
  <h1 class="headline"><span class="year">2023</span> MATERIAL PRICE LIST</h1>

  <!-- Column 1 -->
  <div class="pill" style="left:93px;top:124px;width:67px">SOIL</div>
  <div class="list" style="left:33px;top:143px;width:184px">
    <div class="row"><span class="label">Sandy Loam</span><span class="leader"></span><span class="price"><sup>$</sup>30</span></div>
    <div class="row"><span class="label">Topsoil-Screened</span><span class="leader"></span><span class="price"><sup>$</sup>42</span></div>
    <div class="row"><span class="label">Garden Soil</span><span class="leader"></span><span class="price"><sup>$</sup>52</span></div>
    <div class="row"><span class="label">Mushroom Dirt</span><span class="leader"></span><span class="price"><sup>$</sup>55</span></div>
    <div class="row"><span class="label">Compost (Leaf &amp; Grass)</span><span class="leader"></span><span class="price"><sup>$</sup>55</span></div>
  </div>

  <div class="pill" style="left:93px;top:202px;width:67px">MULCH</div>
  <div class="list" style="left:33px;top:221px;width:184px">
    <div class="row"><span class="label">Mulch-Dyed Black</span><span class="leader"></span><span class="price"><sup>$</sup>42</span></div>
    <div class="row"><span class="label">Mulch-Dyed Red</span><span class="leader"></span><span class="price"><sup>$</sup>42</span></div>
    <div class="row"><span class="label">Mulch-Dyed Brown</span><span class="leader"></span><span class="price"><sup>$</sup>42</span></div>
    <div class="row"><span class="label">Mulch-Natural Light Brown</span><span class="leader"></span><span class="price"><sup>$</sup>38</span></div>
    <div class="row"><span class="label">Mulch-Dark Triple Ground</span><span class="leader"></span><span class="price"><sup>$</sup>44</span></div>
    <div class="row"><span class="label">Mulch Cedar</span><span class="leader"></span><span class="price"><sup>$</sup>44</span></div>
  </div>

  <div class="pill" style="left:53px;top:293px;width:143px">DECORATIVE STONE</div>
  <div class="list" style="left:33px;top:313px;width:184px">
    <div class="row"><span class="label">White Limestone #1 [1/4"-1/2"]</span><span class="leader"></span><span class="price"><sup>$</sup>95</span></div>
    <div class="row"><span class="label">White Limestone #2 [1/2"-3/4"]</span><span class="leader"></span><span class="price"><sup>$</sup>97.50</span></div>
    <div class="row"><span class="label">River Rock #2 [3/4"]</span><span class="leader"></span><span class="price"><sup>$</sup>50</span></div>
    <div class="row"><span class="label">Round River Rock-Medium [2/3"]</span><span class="leader"></span><span class="price"><sup>$</sup>95</span></div>
    <div class="row"><span class="label">River Rounds [4-6"]</span><span class="leader"></span><span class="price"><sup>$</sup>90</span></div>
    <div class="row"><span class="label">Pea Gravel</span><span class="leader"></span><span class="price"><sup>$</sup>50</span></div>
    <div class="row"><span class="label">Berkshire Blend</span><span class="leader"></span><span class="price"><sup>$</sup>120</span></div>
    <div class="row"><span class="label">3/4" Barn Red Stone $127</span><span class="leader"></span><span class="price"><sup>$</sup>127</span></div>
    <div class="row"><span class="label">3/4" Yellow Ocean Gravel</span><span class="leader"></span><span class="price"><sup>$</sup>140</span></div>
    <div class="row"><span class="label">3/4" Delaware River Gravel</span><span class="leader"></span><span class="price"><sup>$</sup>110</span></div>
    <div class="row"><span class="label">1" Nutmeg Pebble</span><span class="leader"></span><span class="price"><sup>$</sup>97</span></div>
  </div>

  <div class="pill" style="left:93px;top:433px;width:67px">SAND</div>
  <div class="list" style="left:33px;top:453px;width:184px">
    <div class="row"><span class="label">Masonary/Pool Sand</span><span class="leader"></span><span class="price"><sup>$</sup>45</span></div>
    <div class="row"><span class="label">Bedding Sand</span><span class="leader"></span><span class="price"><sup>$</sup>37</span></div>
  </div>

  <!-- Column 2 -->
  <div class="pill" style="left:290px;top:124px;width:143px">COMMERCIAL STONE</div>
  <div class="list" style="left:272px;top:143px;width:182px">
    <div class="row"><span class="label">Item #4</span><span class="leader"></span><span class="price"><sup>$</sup>42</span></div>
    <div class="row"><span class="label">#1 Stone (1/2")</span><span class="leader"></span><span class="price"><sup>$</sup>45</span></div>
    <div class="row"><span class="label">#2 Stone (3/4" 1")</span><span class="leader"></span><span class="price"><sup>$</sup>45</span></div>
    <div class="row"><span class="label">#3 (1.5" 2")</span><span class="leader"></span><span class="price"><sup>$</sup>40</span></div>
    <div class="row"><span class="label">Stone Chip (fine)</span><span class="leader"></span><span class="price"><sup>$</sup>47</span></div>
    <div class="row"><span class="label">Stone Dust (xtra fine)</span><span class="leader"></span><span class="price">CALL</span></div>
    <div class="row"><span class="label">Shale When Available</span><span class="leader"></span><span class="price"><sup>$</sup>47</span></div>
    <div class="row"><span class="label">Bank Run Fill (Dirt &amp; Cobble)</span><span class="leader"></span><span class="price"><sup>$</sup>18</span></div>
    <div class="row"><span class="label">Crusher Run</span><span class="leader"></span><span class="price"><sup>$</sup>42</span></div>
    <div class="row"><span class="label">Fill Dirt</span><span class="leader"></span><span class="price"><sup>$</sup>16</span></div>
  </div>

  <div class="pill" style="left:319px;top:255px;width:82px">SEASONAL</div>
  <div class="list" style="left:270px;top:275px;width:184px">
    <div class="row"><span class="label">Treated Salt Green</span><span class="leader"></span><span class="price"><sup>$</sup>165</span></div>
  </div>

  <div class="pill" style="left:290px;top:293px;width:143px">DELIVERY CHARGES</div>
  <div class="list" style="left:272px;top:312px;width:182px">
    <div class="row"><span class="label">Local (Small Truck)</span><span class="leader"></span><span class="price"><sup>$</sup>60</span></div>
    <div class="row"><span class="label">Local (Medium Truck)</span><span class="leader"></span><span class="price"><sup>$</sup>75</span></div>
    <div class="row"><span class="label">Local (Large Truck)</span><span class="leader"></span><span class="price"><sup>$</sup>115</span></div>
    <div class="row small" style="margin-top:2px"><span class="label">Local Delivering 7 Mile Radius</span></div>
    <div class="row small"><span class="label">Excluding the Mut</span></div>
    <div class="row"><span class="label">Non Local</span><span class="leader"></span><span class="price quote">CALL FOR QUOTE</span></div>
  </div>

  <div class="swatch stone" role="img" aria-label="Photo of white limestone gravel" style="left:265px;top:387px"></div>
  <div class="swatch soil" role="img" aria-label="Photo of hands holding dark garden soil" style="left:333px;top:387px"></div>
  <div class="swatch sand" role="img" aria-label="Photo of fine bedding sand" style="left:401px;top:387px"></div>
  <p class="notice">Please note that prices are subject to change<br>without prior notice.</p>

  <!-- Column 3 -->
  <div class="pill tall" style="left:524px;top:125px;width:151px">EQUIPMENT WITH<br>OPERATOR AVAILABLE</div>
  <div class="list" style="left:505px;top:158px;width:187px">
    <div class="row"><span class="label">Onsite Mobile</span><span class="leader"></span><span class="price wide">CALL FOR PRICE</span></div>
    <div class="row"><span class="label">Grinding/Tub Grinding</span><span class="leader"></span><span class="price wide">CALL FOR PRICE</span></div>
    <div class="row"><span class="label">Forestry Mulching</span><span class="leader"></span><span class="price wide">CALL FOR PRICE</span></div>
    <div class="row strong" style="margin-top:1.5px"><span class="label">Skid Steer : (Rubber Track)</span><span class="leader" style="border:0"></span><span class="price wide">CALL FOR PRICE</span></div>
  </div>

  <div class="group" style="left:501px;top:209px;width:192px;height:29px">
    <span class="group-title">AVAILABLE ATTACHMENT</span>
    <div class="ticks" style="top:5px">
      <span class="tick"><svg viewBox="0 0 10 10"><circle cx="5" cy="5" r="5" fill="#1e8c3a"/><path d="M2.6 5.2 L4.3 6.8 L7.4 3.5" stroke="#fff" stroke-width="1.4" fill="none"/></svg>Landscape Rake</span>
      <span class="tick"><svg viewBox="0 0 10 10"><circle cx="5" cy="5" r="5" fill="#1e8c3a"/><path d="M2.6 5.2 L4.3 6.8 L7.4 3.5" stroke="#fff" stroke-width="1.4" fill="none"/></svg>3/4 Yard Bucket</span>
      <span class="tick"><svg viewBox="0 0 10 10"><circle cx="5" cy="5" r="5" fill="#1e8c3a"/><path d="M2.6 5.2 L4.3 6.8 L7.4 3.5" stroke="#fff" stroke-width="1.4" fill="none"/></svg>Grapple Bucket</span>
    </div>
    <div class="ticks" style="top:16px">
      <span class="tick"><svg viewBox="0 0 10 10"><circle cx="5" cy="5" r="5" fill="#1e8c3a"/><path d="M2.6 5.2 L4.3 6.8 L7.4 3.5" stroke="#fff" stroke-width="1.4" fill="none"/></svg>Forestry Mulching</span>
      <span class="tick"><svg viewBox="0 0 10 10"><circle cx="5" cy="5" r="5" fill="#1e8c3a"/><path d="M2.6 5.2 L4.3 6.8 L7.4 3.5" stroke="#fff" stroke-width="1.4" fill="none"/></svg>Hydraulic Auger</span>
    </div>
  </div>

  <div class="group" style="left:501px;top:254px;width:192px;height:61px">
    <span class="group-title">EXCAVATOR</span>
    <div class="list" style="top:5px">
      <div class="row"><span class="label">35 Class (7,500bs)</span><span class="leader"></span><span class="price wide">CALL FOR PRICE</span></div>
      <div class="row"><span class="label">60 Class (14,000bs)</span><span class="leader"></span><span class="price wide">CALL FOR PRICE</span></div>
      <div class="row"><span class="label">140 Class (45,500bs)</span><span class="leader"></span><span class="price wide">CALL FOR PRICE</span></div>
      <div class="row"><span class="label">160 Class (38,500bs)</span><span class="leader"></span><span class="price wide">CALL FOR PRICE</span></div>
      <div class="row"><span class="label">250 Class (60,000bs)</span><span class="leader"></span><span class="price wide">CALL FOR PRICE</span></div>
    </div>
  </div>

  <div class="group" style="left:501px;top:326px;width:192px;height:51px">
    <span class="group-title">BULL DOZER</span>
    <div class="list" style="top:5px">
      <div class="row"><span class="label">450 Class (18,000bs)</span><span class="leader"></span><span class="price wide">CALL FOR PRICE</span></div>
      <div class="row"><span class="label">700 Class (30,000bs)</span><span class="leader"></span><span class="price wide">CALL FOR PRICE</span></div>
      <div class="row"><span class="label">Vibratory Roller</span><span class="leader"></span><span class="price wide">CALL FOR PRICE</span></div>
      <div class="row"><span class="label">Rock Hammer</span><span class="leader"></span><span class="price wide">CALL FOR PRICE</span></div>
    </div>
  </div>

  <p class="note-green" style="top:382px">Hydraulic Rock Hammer on 160 Class excavator.<br>Additional mobilization fee for 1st day</p>
  <div class="list" style="left:505px;top:400px;width:187px">
    <div class="row"><span class="label">Tri-Axle Dump</span><span class="leader"></span><span class="price">CALL</span></div>
    <div class="row"><span class="label">Dump Trailer</span><span class="leader" style="border:0"></span><span class="price">CALL</span></div>
  </div>

  <aside class="tip">
    <div class="tip-icon" role="img" aria-label="Megaphone illustration"></div>
    <p class="tip-title">DID YOU KNOW?</p>
    <p class="tip-body">We Offer Onside Tub Grinding &amp; We are a GREEN RECYCLING Location!<br>NON LOCAL CALL FOR PRICING ALSO THANK YOU</p>
  </aside>

  <p class="site">ridgewaysupply.com</p>
</main>
</body>
</html>
```